Commercial Post Cards

We are looking for 3 postcards that are similar but target 3 commercial property types. they will be 6x9 cards can be front and back or not.
1. Hotel Postcard – Taviqon / Bed Bug Protection
Use the attached Taviqon sample as the primary direction.
The focus should be:
Proactive bed bug prevention and control
Protecting guests and the hotel's reputation
Regular inspections
Documentation and risk management
Professional commercial pest management
The backside should transition into our General Pest Control services, showing that we can be the hotel's complete pest management provider beyond just bed bugs.
2. Apartment Complex Postcard
Target apartment owners, property managers, and management companies.
Focus on:
General pest control
Bed bug control
Rodent control
Preventative pest management
Protecting residents and the property
Reliable, ongoing service and documentation
The message should position us as a full-service pest management partner for multifamily properties.

3. Commercial Building Postcard
Target office buildings, banks, storage facilities, and other commercial properties.

Focus on:
General commercial pest control
Rodent control
Fly management
Recurring service programs
Protecting the property, employees, customers, and reputation

Overall Direction
All three postcards should have a consistent brand and visual style, but each should feel specifically designed for its target market.

We want the messaging to communicate:
Professional • Reliable • Proactive • Locally Owned & Operated • Serving Since 2017

The goal is not to overwhelm the reader with information. These should be marketing pieces that quickly communicate the problem we solve, our expertise, and why a commercial property should contact us.

I have included some of our marketing materials for help with what we do.

```html
<!DOCTYPE html>
<html lang="en">
<head>
<meta charset="utf-8">
<title>General Pest Solutions – Postcard Back</title>
<link href="https://fonts.googleapis.com/css2?family=Bebas+Neue&family=Arimo:wght@400;600;700&display=swap" rel="stylesheet">
<style>
  :root {
    --orange: #fd5416;
    --ink: #222222;
    --text: #2e2e2e;
    --panel: #f3f3f3;
    --paper: #ffffff;
    --rule: #cfcfcf;
    --faint: #c9c9c9;
  }
  * { margin: 0; padding: 0; box-sizing: border-box; }
  html, body { width: 1200px; height: 800px; overflow: hidden; background: var(--paper); }
  .postcard { position: relative; width: 1200px; height: 800px; background: var(--paper); }

  .services-panel { position: absolute; left: 0; top: 0; width: 732px; height: 800px; background: var(--panel); }
  .panel-title {
    position: absolute; left: 0; top: 30px; width: 732px; text-align: center;
    font-family: "Bebas Neue", sans-serif; font-size: 46px; line-height: 50px; color: var(--ink); letter-spacing: 0.2px;
  }
  .panel-title .accent { color: var(--orange); }

  .icon-band { position: absolute; left: 40px; width: 652px; height: 80px; background: var(--orange); display: flex; }
  .icon-band.row-1 { top: 93px; }
  .icon-band.row-2 { top: 377px; }
  .icon-cell { flex: 1; display: flex; align-items: center; justify-content: center; position: relative; }
  .icon-cell + .icon-cell::before {
    content: ""; position: absolute; left: 0; top: 7px; bottom: 7px; width: 1.5px; background: var(--ink);
  }
  .shield { width: 60px; height: 72px; display: block; }

  .service-row { position: absolute; left: 40px; width: 652px; display: flex; }
  .service-row.row-1 { top: 182px; height: 182px; }
  .service-row.row-2 { top: 466px; height: 186px; }
  .service { flex: 1; text-align: center; position: relative; padding: 0 4px; }
  .service + .service::before {
    content: ""; position: absolute; left: 0; top: 0; bottom: 0; width: 1.5px; background: var(--rule);
  }
  .service-name {
    height: 84px; display: flex; align-items: center; justify-content: center;
    font-family: "Bebas Neue", sans-serif; font-weight: 400; font-size: 31px; line-height: 28px;
    color: var(--orange); letter-spacing: -0.2px;
  }
  .service-desc {
    margin-top: 15px; font-family: "Arimo", Arial, sans-serif; font-weight: 600;
    font-size: 15.5px; line-height: 19px; color: var(--text);
  }
  .service-row.row-2 .service-desc { margin-top: 18px; }

  .brand {
    position: absolute; left: 0; top: 688px; width: 732px; display: flex; align-items: center; justify-content: center; gap: 10px;
  }
  .brand-mark { width: 22px; height: 22px; background: var(--orange); }
  .brand-name {
    font-family: "Arimo", Arial, sans-serif; font-weight: 700; font-size: 30px; line-height: 34px; color: var(--ink);
  }

  .values-bar {
    position: absolute; left: 0; top: 743px; width: 732px; height: 57px; background: var(--ink);
    display: flex; align-items: center; justify-content: center;
    font-family: "Bebas Neue", sans-serif; font-size: 24.5px; color: var(--paper); letter-spacing: 0.1px; white-space: nowrap;
  }

  .stamp-box {
    position: absolute; left: 1075px; top: 37px; width: 94px; height: 100px;
    border: 1.5px dashed var(--faint); display: flex; align-items: center; justify-content: center; text-align: center;
    font-family: "Arimo", Arial, sans-serif; font-size: 18px; line-height: 21px; color: var(--faint);
  }
  .address-line { position: absolute; left: 771px; width: 377px; border-top: 1.5px dotted #9a9a9a; }
</style>
</head>
<body>
<main class="postcard">
  <section class="services-panel">
    <h1 class="panel-title">General Pest <span class="accent">Solutions</span></h1>

    <div class="icon-band row-1">
      <div class="icon-cell"><svg class="shield" viewBox="0 0 60 72" role="img" aria-label="Shield icon with an ant"><path d="M30 2 C20 8 10 10 3 10 L3 36 C3 54 17 65 30 70 C43 65 57 54 57 36 L57 10 C50 10 40 8 30 2 Z" fill="#fff"/><path d="M30 8 C22 13 14 15 8 15 L8 36 C8 51 19 60 30 64 C41 60 52 51 52 36 L52 15 C46 15 38 13 30 8 Z" fill="#222"/></svg></div>
      <div class="icon-cell"><svg class="shield" viewBox="0 0 60 72" role="img" aria-label="Shield icon with a mouse"><path d="M30 2 C20 8 10 10 3 10 L3 36 C3 54 17 65 30 70 C43 65 57 54 57 36 L57 10 C50 10 40 8 30 2 Z" fill="#fff"/><path d="M30 8 C22 13 14 15 8 15 L8 36 C8 51 19 60 30 64 C41 60 52 51 52 36 L52 15 C46 15 38 13 30 8 Z" fill="#222"/></svg></div>
      <div class="icon-cell"><svg class="shield" viewBox="0 0 60 72" role="img" aria-label="Shield icon with a bed bug"><path d="M30 2 C20 8 10 10 3 10 L3 36 C3 54 17 65 30 70 C43 65 57 54 57 36 L57 10 C50 10 40 8 30 2 Z" fill="#fff"/><path d="M30 8 C22 13 14 15 8 15 L8 36 C8 51 19 60 30 64 C41 60 52 51 52 36 L52 15 C46 15 38 13 30 8 Z" fill="#222"/></svg></div>
      <div class="icon-cell"><svg class="shield" viewBox="0 0 60 72" role="img" aria-label="Shield icon with a fly"><path d="M30 2 C20 8 10 10 3 10 L3 36 C3 54 17 65 30 70 C43 65 57 54 57 36 L57 10 C50 10 40 8 30 2 Z" fill="#fff"/><path d="M30 8 C22 13 14 15 8 15 L8 36 C8 51 19 60 30 64 C41 60 52 51 52 36 L52 15 C46 15 38 13 30 8 Z" fill="#222"/></svg></div>
    </div>

    <div class="service-row row-1">
      <article class="service"><h2 class="service-name">General<br>Insect<br>Control</h2><p class="service-desc">Ants, spiders,<br>cockroaches,<br>and other<br>common pests</p></article>
      <article class="service"><h2 class="service-name">Mouse &amp;<br>Rodent<br>Control</h2><p class="service-desc">Prevention,<br>control,<br>monitoring,<br>and exclusion</p></article>
      <article class="service"><h2 class="service-name">Bed Bug<br>Control</h2><p class="service-desc">Inspection,<br>treatment,<br>prevention, and<br>ongoing<br>monitoring</p></article>
      <article class="service"><h2 class="service-name">Fly Control &amp;<br>Management</h2><p class="service-desc">Prevention and<br>ongoing fly<br>maintenance</p></article>
    </div>

    <div class="icon-band row-2">
      <div class="icon-cell"><svg class="shield" viewBox="0 0 60 72" role="img" aria-label="Shield icon with a technician taking notes"><path d="M30 2 C20 8 10 10 3 10 L3 36 C3 54 17 65 30 70 C43 65 57 54 57 36 L57 10 C50 10 40 8 30 2 Z" fill="#fff"/><path d="M30 8 C22 13 14 15 8 15 L8 36 C8 51 19 60 30 64 C41 60 52 51 52 36 L52 15 C46 15 38 13 30 8 Z" fill="#222"/></svg></div>
      <div class="icon-cell"><svg class="shield" viewBox="0 0 60 72" role="img" aria-label="Shield icon with a building"><path d="M30 2 C20 8 10 10 3 10 L3 36 C3 54 17 65 30 70 C43 65 57 54 57 36 L57 10 C50 10 40 8 30 2 Z" fill="#fff"/><path d="M30 8 C22 13 14 15 8 15 L8 36 C8 51 19 60 30 64 C41 60 52 51 52 36 L52 15 C46 15 38 13 30 8 Z" fill="#222"/></svg></div>
      <div class="icon-cell"><svg class="shield" viewBox="0 0 60 72" role="img" aria-label="Shield icon with a magnifier and warning sign"><path d="M30 2 C20 8 10 10 3 10 L3 36 C3 54 17 65 30 70 C43 65 57 54 57 36 L57 10 C50 10 40 8 30 2 Z" fill="#fff"/><path d="M30 8 C22 13 14 15 8 15 L8 36 C8 51 19 60 30 64 C41 60 52 51 52 36 L52 15 C46 15 38 13 30 8 Z" fill="#222"/></svg></div>
      <div class="icon-cell"><svg class="shield" viewBox="0 0 60 72" role="img" aria-label="Shield icon with a calendar and clock"><path d="M30 2 C20 8 10 10 3 10 L3 36 C3 54 17 65 30 70 C43 65 57 54 57 36 L57 10 C50 10 40 8 30 2 Z" fill="#fff"/><path d="M30 8 C22 13 14 15 8 15 L8 36 C8 51 19 60 30 64 C41 60 52 51 52 36 L52 15 C46 15 38 13 30 8 Z" fill="#222"/></svg></div>
    </div>

    <div class="service-row row-2">
      <article class="service"><h2 class="service-name">Preventative<br>Pest<br>Management</h2><p class="service-desc">Routine<br>inspections<br>and proactive<br>treatments</p></article>
      <article class="service"><h2 class="service-name">Exterior<br>Pest<br>Control</h2><p class="service-desc">Perimeter<br>treatments to<br>help prevent<br>pests from<br>entering</p></article>
      <article class="service"><h2 class="service-name">Commercial<br>Pest<br>Inspections</h2><p class="service-desc">Identify pest<br>activity and<br>potential risk<br>areas</p></article>
      <article class="service"><h2 class="service-name">Ongoing<br>Service<br>Programs</h2><p class="service-desc">Scheduled<br>service tailored<br>to your<br>property's<br>needs</p></article>
    </div>

    <div class="brand">
      <span class="brand-mark"></span>
      <span class="brand-name">Brevon Pest Control</span>
    </div>

    <footer class="values-bar">Professional • Reliable • Proactive • Locally Owned &amp; Operated • Serving Since 2017</footer>
  </section>

  <section class="mailing-side">
    <div class="stamp-box">PLACE<br>STAMP<br>HERE</div>
    <div class="address-line" style="top:513px"></div>
    <div class="address-line" style="top:570px"></div>
    <div class="address-line" style="top:627px"></div>
    <div class="address-line" style="top:684px"></div>
    <div class="address-line" style="top:741px"></div>
  </section>
</main>
</body>
</html>
```